Satchel & Sundial needs new business card design

I need a new business card design. I'm looking for out-of-the-box design which represents the freedom of being a location independent entrepreneur.
I offer coaching, retreats and trips.
I would like to see designs with and without the photo.
Colors I use are black (#000000), green (#25A796) and brown (#D7C38C)
Website satchelandsundial.example

Target Market(s)

location independent entrepreneurs, digital nomads, people looking to swap the 9 to 5 for a lifestyle business

Industry/Entity Type

Business

Contact Information for Business Card

Dorota Falkner
Your Lifestyle Business Coach, Retreat & Trip Leader
http://satchelandsundial.example
hello@satchelandsundial.example
Live a life you don't need a holiday from

Font styles to use
Serif
Sans Serif

Requirements
Must have
• One side should contain only the logo. I would also consider having the "Live a life you don't need a holiday from" on that side too (depending on how it looks)
• Please show both sides on the designs.

```html
<!DOCTYPE html>
<html lang="en">
<head>
<meta charset="utf-8">
<title>Satchel &amp; Sundial — Business Card</title>
<link rel="stylesheet" href="https://fonts.googleapis.com/css2?family=Oswald:wght@400;500;600&family=Roboto:wght@400&display=swap">
<style>
  :root {
    --ink: #000000;
    --ink-soft: #1a1a1a;
    --teal: #25A796;
    --teal-deep: #128a7c;
    --sand: #D7C38C;
    --paper: #f7f7f7;
    --backdrop: #dedede;
    --white: #ffffff;
  }
  * { margin: 0; padding: 0; box-sizing: border-box; }
  html, body { width: 1200px; height: 576px; overflow: hidden; }
  body { background: var(--backdrop); position: relative; }

  .card {
    position: absolute;
    top: 139px;
    width: 484px;
    height: 293px;
    background: var(--paper);
    border-radius: 8px;
    box-shadow: 0 2px 4px rgba(0,0,0,0.18);
    overflow: hidden;
  }
  .card--front { left: 82px; }
  .card--back { left: 602px; }

  .wordmark {
    font-family: "Oswald", sans-serif;
    font-weight: 500;
    color: var(--ink);
    text-transform: uppercase;
    white-space: nowrap;
    letter-spacing: 0.5px;
  }
  .card--front .wordmark {
    position: absolute;
    left: 0; right: 0;
    top: 118px;
    text-align: center;
    font-size: 36px;
    line-height: 44px;
  }
  .card--back .wordmark {
    position: absolute;
    left: 22px;
    width: 196px;
    top: 116px;
    text-align: center;
    font-size: 21px;
    line-height: 28px;
  }

  .divider {
    position: absolute;
    left: 237px;
    top: 57px;
    width: 1px;
    height: 148px;
    background: var(--sand);
  }

  .contact { position: absolute; left: 272px; top: 67px; font-family: "Oswald", sans-serif; }
  .contact__name {
    font-weight: 600;
    font-size: 20px;
    line-height: 24px;
    color: var(--ink);
    text-transform: uppercase;
  }
  .contact__role {
    margin-top: 2px;
    font-weight: 400;
    font-size: 11.5px;
    line-height: 14.5px;
    color: var(--teal-deep);
  }
  .contact__list { list-style: none; margin-top: 9px; }
  .contact__item {
    display: flex;
    align-items: center;
    gap: 7px;
    font-weight: 400;
    font-size: 12px;
    line-height: 20px;
    color: var(--ink-soft);
  }
  .contact__item svg { flex: none; }
  .contact__item--social { color: var(--teal-deep); margin-top: 1px; }
  .social-mark { width: 9px; height: 9px; background: var(--ink-soft); border-radius: 1px; flex: none; }

  .footer-bands { position: absolute; left: 0; bottom: 0; }
  .tagline {
    position: absolute;
    left: 232px;
    bottom: 9px;
    font-family: "Roboto", sans-serif;
    font-size: 13px;
    line-height: 16px;
    color: var(--white);
    white-space: nowrap;
  }
</style>
</head>
<body>

  <section class="card card--front" aria-label="Card front">
    <div class="wordmark">Satchel &amp; Sundial</div>
  </section>

  <section class="card card--back" aria-label="Card back">
    <div class="wordmark">Satchel &amp; Sundial</div>
    <div class="divider"></div>

    <div class="contact">
      <h1 class="contact__name">Dorota Falkner</h1>
      <p class="contact__role">Your Lifestyle Business Coach<br>Retreat &amp; Trip Leader</p>
      <ul class="contact__list">
        <li class="contact__item">
          <svg width="11" height="8" viewBox="0 0 11 8" aria-hidden="true">
            <rect x="0" y="0" width="11" height="8" fill="var(--teal)"/>
            <path d="M0.5 0.7 L5.5 4.6 L10.5 0.7" fill="none" stroke="var(--paper)" stroke-width="1"/>
          </svg>
          hello@satchelandsundial.example
        </li>
        <li class="contact__item">
          <svg width="10" height="10" viewBox="0 0 10 10" aria-hidden="true">
            <g fill="none" stroke="var(--teal)" stroke-width="1">
              <circle cx="5" cy="5" r="4.4"/>
              <ellipse cx="5" cy="5" rx="1.9" ry="4.4"/>
              <line x1="0.6" y1="5" x2="9.4" y2="5"/>
              <line x1="1.3" y1="2.8" x2="8.7" y2="2.8"/>
              <line x1="1.3" y1="7.2" x2="8.7" y2="7.2"/>
            </g>
          </svg>
          www.satchelandsundial.example
        </li>
        <li class="contact__item contact__item--social">
          <span class="social-mark" aria-hidden="true"></span>
          /satchelandsundial
        </li>
      </ul>
    </div>

    <svg class="footer-bands" width="484" height="37" viewBox="0 0 484 37" aria-hidden="true">
      <rect x="0" y="19" width="205" height="18" fill="var(--teal-deep)"/>
      <polygon points="210,0 484,0 484,37 187,37" fill="var(--ink-soft)"/>
    </svg>
    <p class="tagline">Live a life you don't need a holiday from</p>
  </section>

</body>
</html>
```